Refresh of far from plain IT company website

Our web site is starting to show it's age. You can see the existing site here: www.plumbwick.net. As a growing company we want to come across as a dynamic collection of IT experts.

We want to update the design so are open to any colour palette and look, but want to retain our current table logo. We use the logo on our business cards but with a white background - see the attached file, so you don't need to keep the brown or the green.

The design should consider the range of browsers that will be looking at the site - so please show how it will look on a wide screen laptop and a 768x1024 tablet.

We want to add some pages about our team and their skills, probably with photos of each person on the team.

This is an uncoded project - the PSD files of the design is required, not coding.
Updates

Thanks everyone for the submissions so far.  It's a holiday day in the UK today but we will get some feedback on the designs so far out to you.

Target Market(s)

Architects and other creative types looking for IT support

Industry/Entity Type

Business

Font styles to use
Serif
Sans Serif

Requirements
Must have
• Must look good on a laptop and an iPad.

```html
<!DOCTYPE html>
<html lang="en">
<head>
<meta charset="utf-8">
<title>plumbwick – IT Support For Business</title>
<link rel="stylesheet" href="https://fonts.googleapis.com/css2?family=Open+Sans:ital,wght@0,400;0,600;0,700;1,400;1,600&family=Tinos:ital,wght@0,400;0,700;1,400;1,700&display=swap">
<style>
:root{
  --plum:#8c0f47;
  --gold:#deaa06;
  --text:#6b6b6b;
  --dark:#222;
  --band:#0b131b;
  --footer:#2e2e2e;
  --line:#e4e4e4;
  --serif:'Tinos', 'Times New Roman', serif;
  --sans:'Open Sans', Arial, sans-serif;
}
*{box-sizing:border-box;margin:0;padding:0}
html,body{width:1200px;height:2769px;overflow:hidden;background:#fff}
.page{position:relative;width:1200px;height:2769px;overflow:hidden;font-family:var(--sans);color:var(--text)}
.abs{position:absolute}
.topline{left:0;top:0;width:1200px;height:5px;background:var(--plum)}
.brand{left:133px;top:28px;display:flex;align-items:center;gap:12px}
.brand-mark{width:36px;height:36px;background:var(--gold)}
.brand-name{font:700 34px var(--sans);color:var(--plum);letter-spacing:-.5px}
.nav{top:40px;font:400 15px var(--sans);color:var(--dark)}
.hero{left:0;top:96px;width:1200px;height:620px;background:linear-gradient(180deg,#dfe8ee 0%,#c9d6de 40%,#b4c3cc 75%,#d9e0e4 100%)}
.hero-arrow{top:360px}
.hero-title{left:0;top:585px;width:1200px;text-align:center;font:italic 700 44px var(--serif);color:var(--plum)}
.heading{left:0;width:1200px;text-align:center;font:400 22px var(--serif);color:var(--plum)}
.intro{left:166px;top:802px;width:868px;text-align:center;font:italic 600 11px/30px var(--sans);color:#777}
.service{width:240px;text-align:center}
.service-icon{width:84px;height:84px;border-radius:50%;background:var(--gold);margin:0 auto;display:flex;align-items:center;justify-content:center}
.service-title{margin-top:30px;font:400 15px var(--serif);color:var(--plum)}
.service-text{margin-top:16px;font:400 11.5px/26px var(--sans);color:#777}
.band{left:0;top:1218px;width:1200px;height:364px;background:radial-gradient(ellipse at 50% 40%,#1a2733 0%,var(--band) 70%)}
.band-title{left:0;top:1250px;width:1200px;text-align:center;font:400 24px var(--serif);color:#fff}
.band-text{left:150px;top:1312px;width:900px;text-align:center;font:400 11.5px/37px var(--sans);color:#fff}
.band-btn{left:460px;top:1484px;width:280px;height:48px;border:1.5px solid #fff;border-radius:4px;display:flex;align-items:center;justify-content:center;font:italic 700 18px var(--serif);color:#fff}
.card{top:1661px;width:284px;height:194px;border:1px solid var(--line);padding:12px}
.card-photo{width:100%;height:100%}
.art-title{top:1876px;width:290px;font:400 15px var(--serif);color:var(--gold)}
.art-text{top:1908px;width:290px;font:400 11.5px/25px var(--sans);color:#777}
.art-text em{color:var(--plum);font-weight:600}
.col-head{top:2070px;font:400 21px var(--serif);color:var(--plum)}
.blog-photo{left:131px;top:2114px;width:292px;height:166px;background:linear-gradient(180deg,#6f9ccc 0%,#a9c6e2 55%,#d6dde4 100%)}
.blog-title{left:131px;top:2296px;font:400 14px var(--serif);color:var(--gold)}
.blog-date{left:131px;top:2322px;font:400 12px var(--serif);color:var(--dark)}
.blog-date b{font-weight:700}
.blog-text{left:131px;top:2353px;width:300px;font:400 11.5px/27px var(--sans);color:#777}
.blog-text em{font-weight:700;color:var(--plum)}
.quote-mark{font:400 34px var(--serif);color:#555}
.quote-text{left:465px;top:2124px;width:280px;font:400 11.5px/22px var(--sans);color:#777}
.avatar{left:456px;top:2271px;width:96px;height:96px;border-radius:50%;border:1px solid #ccc;background:linear-gradient(180deg,#e9ecef,#c7cdd3)}
.p-name{left:578px;top:2298px;font:italic 700 14px var(--serif);color:var(--gold)}
.p-date{left:578px;top:2324px;font:400 12px var(--sans);color:#777}
.news{left:770px;width:296px;height:121px;display:flex;gap:22px;border-bottom:1px solid var(--line);overflow:hidden}
.news-date{flex:0 0 34px;text-align:center;color:#555;font-family:var(--serif)}
.news-date .d{font:700 22px var(--serif);display:block;line-height:22px}
.news-date .m{font:italic 20px var(--serif);display:block;line-height:22px}
.news-date .y{font:400 12px var(--sans);display:block}
.news-body{flex:1}
.news-title{font:400 12px/20px var(--sans);color:var(--gold)}
.news-text{margin-top:6px;font:400 11.5px/23px var(--sans);color:#777}
.newsletter{left:129px;top:2448px;width:938px;height:131px;border:1px solid #e6e6e6;background:linear-gradient(180deg,#fff,#eee)}
.nl-label{left:144px;top:2492px;font:italic 700 31px var(--serif);color:var(--plum)}
.nl-input{left:404px;top:2490px;width:460px;height:48px;border:1px solid #ccc;background:#fff;padding-left:14px;display:flex;align-items:center;font:400 12px var(--serif);color:#333}
.nl-btn{left:892px;top:2490px;width:160px;height:48px;background:var(--gold);display:flex;align-items:center;justify-content:center;font:400 15px var(--serif);color:#fff;letter-spacing:.5px}
.footer{left:0;top:2590px;width:1200px;height:179px;background:var(--footer)}
.social{top:2614px;width:34px;height:34px;border:2px solid #fff;border-radius:50%}
.foot-nav{left:0;top:2674px;width:1200px;text-align:center;font:400 11px var(--sans);color:#fff}
.foot-nav .sep{margin:0 14px}
.copyright{left:0;top:2720px;width:1200px;text-align:center;font:400 11px var(--sans);color:#fff}
</style>
</head>
<body>
<div class="page">
  <div class="abs topline"></div>

  <header>
    <div class="abs brand"><span class="brand-mark"></span><span class="brand-name">plumbwick</span></div>
    <nav>
      <span class="abs nav" style="left:481px">Home</span>
      <span class="abs nav" style="left:554px">About us</span>
      <span class="abs nav" style="left:644px">What we do</span>
      <span class="abs nav" style="left:753px">News blog</span>
      <span class="abs nav" style="left:852px">Articles</span>
      <span class="abs nav" style="left:931px">Clients</span>
      <span class="abs nav" style="left:1011px">Partners</span>
    </nav>
  </header>

  <section>
    <div class="abs hero" role="img" aria-label="Photo of a smiling business team giving thumbs up"></div>
    <svg class="abs hero-arrow" style="left:44px" width="34" height="94" viewBox="0 0 34 94"><polyline points="30,4 6,47 30,90" fill="none" stroke="#777" stroke-width="4"/></svg>
    <svg class="abs hero-arrow" style="left:1124px" width="34" height="94" viewBox="0 0 34 94"><polyline points="4,4 28,47 4,90" fill="none" stroke="#777" stroke-width="4"/></svg>
    <h1 class="abs hero-title">Serious It Support For Business</h1>
  </section>

  <section>
    <h2 class="abs heading" style="top:752px">Welcome to It Support Business</h2>
    <p class="abs intro">Plumbwick was established with a specific aim: to consistently deliver an advanced and comprehensive IT service for ambitious growing companies across many industry support, and to aid business growth through the effective and skilled use of modern IT solutions.</p>
  </section>

  <section>
    <h2 class="abs heading" style="top:900px">Our Services</h2>
    <div class="abs service" style="left:120px;top:970px">
      <div class="service-icon"><svg width="44" height="44" viewBox="0 0 44 44" fill="none" stroke="#fff" stroke-width="2.5"><circle cx="22" cy="10" r="5"/><circle cx="9" cy="32" r="5"/><circle cx="35" cy="32" r="5"/><path d="M22 15v8M22 23L11 28M22 23l11 5"/></svg></div>
      <h3 class="service-title">It Support &amp; Management</h3>
      <p class="service-text">Plumbwick was established with a speaim: to consistently deliver an and compre-hensive IT service</p>
    </div>
    <div class="abs service" style="left:360px;top:970px">
      <div class="service-icon"><svg width="46" height="40" viewBox="0 0 46 40" fill="none" stroke="#fff" stroke-width="2.5"><rect x="4" y="16" width="26" height="18"/><path d="M12 34v4h10v-4"/><path d="M22 14a8 8 0 0 1 15-2a6 6 0 0 1 3 11h-8"/></svg></div>
      <h3 class="service-title">Cloud Computing</h3>
      <p class="service-text">Plumbwick was established with a speaim: to consistently deliver an and compre-hensive IT service</p>
    </div>
    <div class="abs service" style="left:600px;top:970px">
      <div class="service-icon"><svg width="44" height="40" viewBox="0 0 44 40" fill="#fff"><path d="M22 3L3 20h6v17h26V20h6z"/><rect x="18" y="24" width="8" height="13" fill="var(--gold)"/></svg></div>
      <h3 class="service-title">Disaster Recovery</h3>
      <p class="service-text">Plumbwick was established with a speaim: to consistently deliver an and compre-hensive IT service</p>
    </div>
    <div class="abs service" style="left:840px;top:970px">
      <div class="service-icon"><svg width="44" height="44" viewBox="0 0 44 44" fill="none" stroke="#fff"><circle cx="17" cy="26" r="9" stroke-width="5" stroke-dasharray="4 3"/><circle cx="17" cy="26" r="3" stroke-width="2"/><circle cx="32" cy="12" r="6" stroke-width="4" stroke-dasharray="3 2.5"/></svg></div>
      <h3 class="service-title">Cad Services</h3>
      <p class="service-text">Plumbwick was established with a speaim: to consistently deliver an and compre-hensive IT service</p>
    </div>
  </section>

  <section>
    <div class="abs band" role="img" aria-label="Dark background photo of chess pieces"></div>
    <h2 class="abs band-title">What we do</h2>
    <p class="abs band-text">We are distinctly different, in that we can provide the total IT solution, with good relationships for many years with a strong portfolio of suppliers. Talk to us. We are in an ideal position to be a valuable business partner to you, and add value to your operation today and most importantly to help you effectively plan for the future. Your success is our success.The method used is based on integrating your knowledge of your business with our IT expertise and experience. Result - a unique solution.Utilizing our wealth of experience, Plumbwick have spent many years perfecting the Plumbwick Solution, enabling businesses to progress</p>
    <div class="abs band-btn">Click &nbsp;Here For More Info</div>
  </section>

  <section>
    <h2 class="abs heading" style="top:1610px">Latest Articles</h2>
    <div class="abs card" style="left:133px"><div class="card-photo" role="img" aria-label="Photo of two colleagues working at a laptop" style="background:linear-gradient(135deg,#f2f4f5,#c9d2d8 60%,#9aa7b0)"></div></div>
    <div class="abs card" style="left:458px"><div class="card-photo" role="img" aria-label="Photo of hands over business charts on a desk" style="background:linear-gradient(135deg,#d8e6ec,#8fb6c9 55%,#4b6f84)"></div></div>
    <div class="abs card" style="left:783px"><div class="card-photo" role="img" aria-label="Photo of a businessman in front of glass towers" style="background:linear-gradient(180deg,#3d7bc4,#8ab9e3 50%,#d5e4ef)"></div></div>

    <h3 class="abs art-title" style="left:133px">Client / Server Networks</h3>
    <p class="abs art-text" style="left:133px">Plumbwick's mission is to be the premier IT services partner and provider of software, hardware and sup-port solutions for gressive businesses gressive busi-nesses. ....<em>1 Month ago</em></p>
    <h3 class="abs art-title" style="left:460px">Data And Voice Convergence</h3>
    <p class="abs art-text" style="left:460px">Plumbwick's mission is to be the premier IT services partner and provider of software, hardware and sup-port solutions for gressive businesses gressive busi-nesses. ....<em>1 Month ago</em></p>
    <h3 class="abs art-title" style="left:785px">Multi - Site Connectivity</h3>
    <p class="abs art-text" style="left:785px">Plumbwick's mission is to be the premier IT services partner and provider of software, hardware and sup-port solutions for gressive businesses gressive busi-nesses. ....<em>1 Month ago</em></p>
  </section>

  <section>
    <h2 class="abs col-head" style="left:131px">Blog</h2>
    <div class="abs blog-photo" role="img" aria-label="Illustration of business people beside rising bar columns"></div>
    <h3 class="abs blog-title">Brightlane Certified Installation Engineers</h3>
    <p class="abs blog-date">On Mar 11, 2014 by <b>admin</b></p>
    <p class="abs blog-text">Plumbwick have released phone and tablet apps that allow customers to submit and track support requests on their smart phones. <em>Read More</em></p>

    <h2 class="abs col-head" style="left:452px">Our Partners</h2>
    <span class="abs quote-mark" style="left:442px;top:2112px">&ldquo;</span>
    <p class="abs quote-text">There are many variations of passages of Lorem Ipsum available, but the majority have suffered alteration in some form, by injected humour, or randomised words which don't look even slightly believable. If you are going to use a passage of you isn't in the middle ........</p>
    <span class="abs quote-mark" style="left:592px;top:2226px">&rdquo;</span>
    <div class="abs avatar" role="img" aria-label="Portrait photo of partner"></div>
    <p class="abs p-name">Marcus Hale</p>
    <p class="abs p-date">on 22 Mar 2014</p>

    <h2 class="abs col-head" style="left:770px">Latest News</h2>
    <div class="abs news" style="top:2124px">
      <div class="news-date"><span class="d">25</span><span class="m">Mar</span><span class="y">2014</span></div>
      <div class="news-body"><p class="news-title">Plumbwick phone and tablet App launched....</p><p class="news-text">Plumbwick have released phone and tablet apps that allow support requests on their smart phones.</p></div>
    </div>
    <div class="abs news" style="top:2266px">
      <div class="news-date"><span class="d">25</span><span class="m">Mar</span><span class="y">2014</span></div>
      <div class="news-body"><p class="news-title">Plumbwick phone and tablet App launched....</p><p class="news-text">Plumbwick have released phone and tablet apps that allow support requests on their smart phones.</p></div>
    </div>
  </section>

  <section>
    <div class="abs newsletter"></div>
    <p class="abs nl-label">Newsletter Sign up :</p>
    <div class="abs nl-input">Enter Your Email ID :</div>
    <div class="abs nl-btn">SUBSCRIBE</div>
  </section>

  <footer>
    <div class="abs footer"></div>
    <span class="abs social" style="left:502px"></span>
    <span class="abs social" style="left:542px"></span>
    <span class="abs social" style="left:583px"></span>
    <span class="abs social" style="left:624px"></span>
    <span class="abs social" style="left:664px"></span>
    <p class="abs foot-nav">Home<span class="sep">/</span>About us<span class="sep">/</span>What we do<span class="sep">/</span>News blog<span class="sep">/</span>Articles<span class="sep">/</span>Clients<span class="sep">/</span>Partners</p>
    <p class="abs copyright">Copyright 2014Plumbwick.All Right Reseved.</p>
  </footer>
</div>
</body>
</html>
```